Small Business Broker Business Card Design

A business card design for a small business brokerage, which is a financial service, not unlike real estate brokerage, but for small businesses such as laundromats, pizza shops, restaurants, cleaners etc. The designs should all be simple, more conservative in nature, using the colors and font of the logo. Again, think real estate Brokerage as a business context
Contact Information for Business Card
Name: Glen R. Harlow. Title: Small Business Advisor. Email: g.harlow@bayfieldcapitalworks.example. Mobile: (555) 274-3918. Office: (555) 806-2147. www.bayfieldcapitalworks.example

```html
<!DOCTYPE html>
<html lang="en">
<head>
<meta charset="utf-8">
<title>Bayfield Capital Works – Business Card</title>
<link href="https://fonts.googleapis.com/css2?family=Montserrat:wght@400;500;700&display=swap" rel="stylesheet">
<style>
  :root {
    --navy: #1b3a6b;
    --navy-deep: #17315c;
    --navy-faint: #203f72;
    --ink: #1d1d24;
    --paper: #ffffff;
    --backdrop: #9b9b9b;
  }
  * { margin: 0; padding: 0; box-sizing: border-box; }
  html, body {
    width: 1093px; height: 1200px; overflow: hidden;
    background: var(--backdrop);
    font-family: "Montserrat", Arial, sans-serif;
  }
  .card {
    position: absolute; left: 265px;
    width: 582px; height: 364px;
    border-radius: 15px;
  }
  .card--front { top: 225px; background: var(--paper); }
  .card--back { top: 615px; background: var(--navy); }

  .brand {
    position: absolute; left: 33px; width: 218px; top: 150px;
    text-align: center;
  }
  .brand__mark {
    width: 40px; height: 40px; margin: 0 auto 14px;
    background: var(--navy);
  }
  .brand__name {
    font-weight: 700; font-size: 12px; color: var(--navy);
    white-space: nowrap; letter-spacing: 0.1px;
  }

  .divider {
    position: absolute; left: 271px; top: 116px;
    width: 1.5px; height: 148px; background: var(--navy);
  }
  .person { position: absolute; left: 282px; top: 112px; }
  .person__name { font-weight: 700; font-size: 22px; color: var(--navy); line-height: 1.2; }
  .person__title { font-weight: 500; font-size: 13px; color: var(--ink); margin-top: 1px; }

  .contacts { position: absolute; left: 285px; top: 186px; list-style: none; }
  .contacts li {
    display: flex; align-items: center; gap: 8px;
    font-size: 12.5px; color: var(--ink); height: 19.5px; white-space: nowrap;
  }
  .contacts li:nth-child(2) { margin-top: 4px; }
  .contacts svg { width: 12px; height: 12px; fill: var(--navy); flex: none; }

  .back-brand {
    position: absolute; left: 0; right: 0; top: 110px; text-align: center;
  }
  .back-brand__mark {
    width: 92px; height: 92px; margin: 0 auto 26px;
    background: var(--navy-faint);
  }
  .back-brand__name {
    font-weight: 500; font-size: 20px; color: var(--navy-deep);
    letter-spacing: 0.6px; white-space: nowrap;
  }
</style>
</head>
<body>
  <section class="card card--front">
    <div class="brand">
      <div class="brand__mark"></div>
      <div class="brand__name">BAYFIELD CAPITAL WORKS, INC</div>
    </div>

    <div class="divider"></div>

    <div class="person">
      <h1 class="person__name">Glen R. Harlow</h1>
      <p class="person__title">Small Business Advisor</p>
    </div>

    <ul class="contacts">
      <li>
        <svg viewBox="0 0 24 24" aria-hidden="true"><path d="M2 8c0-3 4-5 10-5s10 2 10 5v2h-6V8c-1-1-7-1-8 0v2H2zM6 12l2-2h8l2 2 3 8H3zM12 14a3 3 0 1 0 0 .1z"/></svg>
        (555) 806-2147
      </li>
      <li>
        <svg viewBox="0 0 24 24" aria-hidden="true"><path d="M6.6 10.8a15 15 0 0 0 6.6 6.6l2.2-2.2c.3-.3.7-.4 1-.2 1.1.4 2.3.6 3.6.6.6 0 1 .4 1 1V20c0 .6-.4 1-1 1A17 17 0 0 1 3 4c0-.6.4-1 1-1h3.5c.6 0 1 .4 1 1 0 1.3.2 2.5.6 3.6.1.3 0 .7-.2 1z"/></svg>
        (555) 274-3918
      </li>
      <li>
        <svg viewBox="0 0 24 24" aria-hidden="true"><path d="M2 5h20v2l-10 6L2 7zM2 9l10 6 10-6v10H2z"/></svg>
        g.harlow@bayfieldcapitalworks.example
      </li>
      <li>
        <svg viewBox="0 0 24 24" aria-hidden="true"><path d="M12 2a10 10 0 1 0 0 20 10 10 0 0 0 0-20zm-1 17.9A8 8 0 0 1 4.2 10L9 15v1a2 2 0 0 0 2 2zm6.9-2.5A2 2 0 0 0 16 16h-1v-3a1 1 0 0 0-1-1H8v-2h2a1 1 0 0 0 1-1V7h2a2 2 0 0 0 2-2v-.4a8 8 0 0 1 2.9 12.8z"/></svg>
        www.bayfieldcapitalworks.example
      </li>
    </ul>
  </section>

  <section class="card card--back">
    <div class="back-brand">
      <div class="back-brand__mark"></div>
      <div class="back-brand__name">BAYFIELD CAPITAL WORKS, INC</div>
    </div>
  </section>
</body>
</html>
```